Exciting letterhead design for startup company

We need a A4 letterhead designing.

See attached file which contains the logo (on 3 different coloured backgrounds) and then the address and contact information. It also contains 4 colours that can be used.

Looking for an imaginative design. We are a young, fresh startup website design company so need a letterhead that reflects our industry.

Sans Serif

```html
<!DOCTYPE html>
<html lang="en">
<head>
<meta charset="utf-8">
<title>SiteLoft Letterhead</title>
<link href="https://fonts.googleapis.com/css2?family=Didact+Gothic&display=swap" rel="stylesheet">
<style>
  :root {
    --backdrop: #d7dadd;
    --paper: #f2f2f2;
    --ink-dark: #2e3236;
    --ink-body: #5a5d61;
    --brand-blue: #3b8dc8;
    --signature-blue: #6f7fc6;
  }
  html, body {
    margin: 0;
    width: 1200px;
    height: 1000px;
    overflow: hidden;
    background: var(--backdrop);
    font-family: "Didact Gothic", "Century Gothic", sans-serif;
  }
  .letterhead {
    position: absolute;
    left: 289px;
    top: 63px;
    width: 624px;
    height: 880px;
    background: var(--paper);
    color: var(--ink-body);
  }
  .brand-name {
    position: absolute;
    left: 60px;
    top: 48px;
    margin: 0;
    font-size: 34px;
    font-weight: 400;
    letter-spacing: -0.5px;
    color: var(--ink-dark);
  }
  .sender-address {
    position: absolute;
    right: 57px;
    top: 54px;
    margin: 0;
    font-style: normal;
    text-align: right;
    font-size: 9.5px;
    line-height: 10.6px;
    color: var(--ink-body);
  }
  .letter-body {
    position: absolute;
    left: 60px;
    top: 292px;
    width: 507px;
    font-size: 9.9px;
    letter-spacing: 0.1px;
    line-height: 10.7px;
  }
  .salutation {
    margin: 0 0 9px;
    font-weight: 700;
    color: var(--ink-dark);
  }
  .letter-body p.paragraph {
    margin: 0 0 10px;
    text-align: justify;
  }
  .sign-off {
    position: absolute;
    left: 60px;
    top: 563px;
    font-size: 9.6px;
    line-height: 11px;
  }
  .sign-off .signer {
    font-weight: 700;
    color: var(--ink-dark);
    display: block;
  }
  .signature {
    position: absolute;
    left: 134px;
    top: 550px;
    width: 130px;
    height: 66px;
    background: linear-gradient(90deg, rgba(111,127,198,0.18), rgba(111,127,198,0.08));
    border-radius: 4px;
  }
  .contact-bar {
    position: absolute;
    left: 60px;
    right: 57px;
    top: 840px;
    display: flex;
    align-items: center;
    font-size: 9px;
    color: var(--ink-dark);
  }
  .contact-item {
    display: flex;
    align-items: center;
    margin-right: 12px;
  }
  .contact-item svg { margin-right: 4px; }
  .contact-web { margin-left: auto; }
  .contact-web strong { color: var(--ink-dark); }
  .contact-web .accent { color: var(--brand-blue); font-weight: 700; }
  .footer-band {
    position: absolute;
    bottom: 0;
    height: 15px;
  }
  .footer-band.dark { left: 0; width: 411px; background: var(--ink-dark); }
  .footer-band.blue { left: 415px; right: 0; background: var(--brand-blue); }
</style>
</head>
<body>
  <main class="letterhead">
    <h1 class="brand-name">SiteLoft</h1>

    <address class="sender-address">
      Unit 4, Harbour Court<br>
      Canal Row, Leeds<br>
      LS1 4QX, United Kingdom
    </address>

    <section class="letter-body">
      <p class="salutation">Dear sir,</p>
      <p class="paragraph">Communication is a very integral part of living creatures, animals and humans. Communication may be verbal or written. Written communication however is only applicable to human beings. Can you even imagine a world without communication? Verbal communication can be through telephones, webcams or in person. Written communication is through letters, emails and mobile phone messages.</p>
      <p class="paragraph">In today's world of great inventions and technology, letters have somehow become redundant. It is the time for text messages or chats. But they still can communicate a lot more than all other modes of communication. Organizations and various government departments still bank on letters as a strong medium of communication. There is no comparison in costs of sending letters as compared to costs of mobile phone messages though – letters are far cheaper. Letters now commonly known as "hard copy documents" are considered more relevant and important than email copies of text messages as proof or evidence of some sort.</p>
      <p class="paragraph">Letters speak volumes about a person or an organization that writes it. So one must take utmost care ensuring that the language used in any letter is appropriate for the occasion for which it is being written. Since a letter is also a written proof or document, if there are certain things that should not form a part of it, then that too should be carefully handled.</p>
      <p class="paragraph">Writing a good letter is an art. But if for some reason someone is unable to write that perfect letter, these different types of letters provide a base for you to build on. Sample letters have been given for everyone to understand what all information needs to form a part of the letter type and then it can be customized.</p>
    </section>

    <div class="sign-off">
      Yours Sincerely,
      <span class="signer">Dara Whitfield</span>
    </div>
    <div class="signature" role="img" aria-label="Handwritten signature of the sender"></div>

    <footer class="contact-bar">
      <span class="contact-item">
        <svg width="9" height="9" viewBox="0 0 10 10" aria-hidden="true">
          <rect width="10" height="10" rx="1.5" fill="var(--brand-blue)"/>
          <path d="M3 2.2c.4-.3.8-.2 1 .2l.5 1c.1.3 0 .6-.3.8l-.3.2c.3.7.8 1.2 1.5 1.5l.2-.3c.2-.3.5-.4.8-.3l1 .5c.4.2.5.6.2 1-.5.7-1.3.9-2.1.5C4.5 6.6 3.4 5.5 2.7 4.3c-.4-.8-.2-1.6.3-2.1z" fill="#fff"/>
        </svg>
        0845 210 7730
      </span>
      <span class="contact-item">
        <svg width="9" height="9" viewBox="0 0 10 10" aria-hidden="true">
          <rect width="10" height="10" rx="1.5" fill="var(--brand-blue)"/>
          <rect x="2" y="3" width="6" height="4.2" fill="none" stroke="#fff" stroke-width="0.8"/>
          <path d="M2 3l3 2.3L8 3" fill="none" stroke="#fff" stroke-width="0.8"/>
        </svg>
        hello@siteloft.co.uk
      </span>
      <span class="contact-item">
        <svg width="9" height="9" viewBox="0 0 10 10" aria-hidden="true">
          <rect width="10" height="10" rx="1.5" fill="var(--brand-blue)"/>
        </svg>
        @siteloft
      </span>
      <span class="contact-web">www.<strong>site</strong><span class="accent">loft</span>.co.uk</span>
    </footer>

    <div class="footer-band dark"></div>
    <div class="footer-band blue"></div>
  </main>
</body>
</html>
```